BOLD & MINIMALIST DESIGN NEEDED

We want a very bold but minimalistic business card design that is impactful and utilizes both sides of the business card. Our current logo is included for your use.

We want bold fonts and good use of negative space. We don't want the logo to overpower the design.

Target Market(s)

Professionals who are building new commercial buildings.

Industry/Entity Type

Construction

Contact Information for Business Card

Name, Title, email, office phone, cell phone, website

Font styles to use
Serif
Sans Serif

Requirements
Must have
• Bold design!

```html
<!DOCTYPE html>
<html lang="en">
<head>
<meta charset="utf-8">
<title>Ridgeway Business Card</title>
<link href="https://fonts.googleapis.com/css2?family=Montserrat:wght@400;500;700;800&display=swap" rel="stylesheet">
<style>
  :root {
    --stage: #3a3a3a;
    --card: #1f1f1f;
    --ink-white: #ffffff;
    --ink-green: #7cc242;
    --ink-green-pale: #d4ebc0;
    --spot-gloss: #2c2c2c;
  }
  * { box-sizing: border-box; margin: 0; padding: 0; }
  html, body {
    width: 1200px; height: 875px; overflow: hidden;
    background: var(--stage);
    font-family: "Montserrat", sans-serif;
  }
  .canvas {
    position: relative; width: 1200px; height: 875px;
  }
  .card {
    position: absolute; width: 540px; height: 308px;
    background: var(--card); border-radius: 16px;
    box-shadow: 0 14px 30px rgba(0,0,0,.45);
    overflow: hidden;
  }
  .card--front { left: 40px; top: 130px; }
  .card--back  { left: 620px; top: 437px; }

  .wordmark {
    position: absolute; display: flex; align-items: center; gap: 12px;
    font-weight: 800; letter-spacing: 1px; text-transform: uppercase;
  }
  .wordmark__square { width: 18px; height: 18px; background: var(--ink-green); }
  .card--front .wordmark {
    left: 50%; top: 50%; transform: translate(-50%, -50%);
    font-size: 54px; color: var(--spot-gloss);
  }
  .card--back .wordmark {
    right: 34px; top: 58px; font-size: 34px; color: var(--ink-white);
  }
  .card--back .wordmark__square { width: 14px; height: 14px; }

  .contact { position: absolute; left: 40px; bottom: 36px; color: var(--ink-white); }
  .contact__name {
    font-size: 26px; font-weight: 700; color: var(--ink-green);
    text-transform: uppercase; letter-spacing: .5px; line-height: 1;
  }
  .contact__title { font-size: 14px; font-weight: 500; margin-top: 6px; }
  .contact__rule { width: 12px; height: 2px; background: var(--ink-green); margin: 12px 0 10px; }
  .contact__list { list-style: none; font-size: 13.5px; font-weight: 500; }
  .contact__list li { display: flex; align-items: center; gap: 8px; line-height: 21px; }
  .contact__list svg { width: 11px; height: 11px; fill: var(--ink-green); flex: none; }

  .web {
    position: absolute; right: 30px; bottom: 66px;
    display: flex; align-items: center; gap: 7px;
    font-size: 14px; font-weight: 500; color: var(--ink-white);
  }
  .web svg { width: 12px; height: 12px; }
  .web__domain { color: var(--ink-green); }
  .web-bar {
    position: absolute; right: 30px; bottom: 44px; width: 200px; height: 10px;
    background: linear-gradient(90deg, var(--ink-green-pale), var(--ink-green));
  }
</style>
</head>
<body>
<main class="canvas">
  <section class="card card--front" aria-label="Card front">
    <div class="wordmark"><span class="wordmark__square"></span>Ridgeway</div>
  </section>

  <section class="card card--back" aria-label="Card back">
    <div class="wordmark"><span class="wordmark__square"></span>Ridgeway</div>

    <div class="contact">
      <h1 class="contact__name">Dana Whitfield</h1>
      <p class="contact__title">Owner/CEO</p>
      <div class="contact__rule"></div>
      <ul class="contact__list">
        <li><svg viewBox="0 0 24 24"><path d="M6.6 10.8a15.1 15.1 0 0 0 6.6 6.6l2.2-2.2a1 1 0 0 1 1-.25 11.4 11.4 0 0 0 3.6.57 1 1 0 0 1 1 1V20a1 1 0 0 1-1 1A17 17 0 0 1 3 4a1 1 0 0 1 1-1h3.5a1 1 0 0 1 1 1 11.4 11.4 0 0 0 .57 3.6 1 1 0 0 1-.25 1z"/></svg>07 5550 1200</li>
        <li><svg viewBox="0 0 24 24"><path d="M7 1h10a2 2 0 0 1 2 2v18a2 2 0 0 1-2 2H7a2 2 0 0 1-2-2V3a2 2 0 0 1 2-2zm0 3v14h10V4z"/></svg>0400 555 019</li>
        <li><svg viewBox="0 0 24 24"><path d="M2 5h20v14H2zm2 2v.5l8 5 8-5V7l-8 5z"/></svg>info@ridgewaybuild.com</li>
      </ul>
    </div>

    <div class="web">
      <svg viewBox="0 0 24 24"><circle cx="12" cy="12" r="10" fill="var(--ink-green)"/><path d="M2 12h20M12 2c3 3 3 17 0 20M12 2c-3 3-3 17 0 20" stroke="var(--card)" stroke-width="1.6" fill="none"/></svg>
      <span>www.<span class="web__domain">ridgewaybuild</span>.com</span>
    </div>
    <div class="web-bar"></div>
  </section>
</main>
</body>
</html>
```